Internal Company (Private/Invite only) blog

I need a template for an internal company blog.
We are an FMCG organisation operating in Saudi Arabia. We have large number of partners working with us across multiple countries.
This blog is primarily designed to inform our shareholders of progress/updates, new information etc.
It will be published/updated weekly

Target Market(s)

audience is company stakeholders only

Industry/Entity Type

It Company

Requirements
Must have
• - Core feature must be that this can be secure/private as we wish to submit information that is only for a registered list of readers.

- ability to update content with images and content
Nice to have
• Some elements we have thought of
- Contact details
- Personnel Bio's
- Weekly product review
- Status on activities
- Case studies
- Future discussion points
- Glossary of terms
- submit your question/idea

Also would like to have ability to have published posts sent to the readers either as a link or as an email with the new content in the message body of the email
Should not have
• No complicated interface.
Should be easy, clean and simple layout
No business type imagery such as pie charts, graphs etc

```html
<!DOCTYPE html>
<html lang="en">
<head>
<meta charset="utf-8">
<title>Brightway Internal Company Blog</title>
<link rel="stylesheet" href="https://fonts.googleapis.com/css2?family=Jost:wght@900&family=Roboto+Condensed:wght@700&family=Arimo&family=Tinos&display=swap">
<style>
  :root {
    --sky-top: #cfe9f7;
    --sky-bottom: #f4fafd;
    --brand-blue: #1a6cc4;
    --headline-blue: #1d6fc2;
    --nav-top: #4aa6f5;
    --nav-bottom: #0b5bbd;
    --nav-edge: #0a4f9e;
    --nav-divider: rgba(0, 40, 100, 0.45);
    --nav-highlight: rgba(255, 255, 255, 0.25);
    --hero-top: #b3dbe4;
    --hero-mid: #8fb4bd;
    --hero-bottom: #56676d;
    --art-top: #9fc3cc;
    --art-bottom: #6f8a92;
    --accent-orange: #f39a1e;
    --text-dark: #333a2e;
    --white: #ffffff;
  }
  * { box-sizing: border-box; margin: 0; padding: 0; }
  html, body { width: 1200px; height: 531px; overflow: hidden; }
  body {
    position: relative;
    background: linear-gradient(180deg, var(--sky-top) 0%, var(--sky-bottom) 100%);
    font-family: "Tinos", serif;
  }
  .brand {
    position: absolute; left: 27px; top: 26px;
    font-family: "Roboto Condensed", sans-serif; font-weight: 700;
    color: var(--brand-blue); text-transform: uppercase;
    line-height: 1;
  }
  .brand-top { display: block; font-size: 31px; }
  .brand-bottom { display: block; font-size: 38px; letter-spacing: 2px; margin-top: 0; }
  .hotline {
    position: absolute; left: 913px; top: 19px;
    display: flex; align-items: center; gap: 12px;
  }
  .hotline-icon { width: 50px; height: 50px; }
  .hotline-number {
    font-family: "Arimo", sans-serif; font-size: 25px; color: var(--text-dark);
  }
  .main-nav {
    position: absolute; left: 16px; top: 106px; width: 1158px; height: 52px;
    display: flex; border-radius: 11px; overflow: hidden;
    background: linear-gradient(180deg, var(--nav-top) 0%, var(--nav-bottom) 100%);
    border: 1px solid var(--nav-edge);
    box-shadow: 0 2px 3px rgba(0, 60, 120, 0.25);
  }
  .main-nav a {
    display: flex; align-items: center; justify-content: center;
    color: var(--white); text-decoration: none; font-size: 17px;
    border-right: 1px solid var(--nav-divider);
    box-shadow: inset 1px 0 0 var(--nav-highlight);
  }
  .main-nav a:last-child { border-right: none; }
  .hero {
    position: absolute; left: 16px; top: 167px; width: 1158px; height: 352px;
    border-radius: 11px; overflow: hidden;
    border: 1px solid #8aa3ab;
    background:
      radial-gradient(ellipse 70% 80% at 30% 5%, rgba(215, 240, 246, 0.7) 0%, rgba(215, 240, 246, 0) 70%),
      linear-gradient(180deg, var(--hero-top) 0%, var(--hero-mid) 50%, var(--hero-bottom) 100%);
  }
  .hero-title {
    position: absolute; left: 35px; top: 70px;
    font-family: "Jost", sans-serif; font-weight: 900;
    font-size: 72px; line-height: 59px; text-transform: uppercase;
    color: var(--headline-blue);
    -webkit-text-stroke: 7px var(--white);
    paint-order: stroke fill;
    letter-spacing: -2.5px;
    text-shadow: 0 3px 6px rgba(0, 40, 80, 0.35);
  }
  .hero-art {
    position: absolute; left: 712px; top: 16px; width: 396px; height: 320px;
    border-radius: 10px;
    background: linear-gradient(180deg, var(--art-top) 0%, var(--art-bottom) 100%);
    opacity: 0.55;
  }
</style>
</head>
<body>
  <header>
    <div class="brand">
      <span class="brand-top">Brightway Internal</span>
      <span class="brand-bottom">Company Blog</span>
    </div>
    <div class="hotline">
      <svg class="hotline-icon" viewBox="0 0 50 50" aria-hidden="true">
        <rect x="2" y="2" width="46" height="46" rx="9" fill="var(--accent-orange)"/>
        <path d="M17 13c2 0 3 4 3.5 6 .3 1.3-1.5 2.5-2 3.5 1.5 3.5 4.5 6.5 8 8 1-.5 2.2-2.3 3.5-2 2 .5 6 1.5 6 3.5 0 2.5-2.5 5-5 5C20 37 13 30 13 18c0-2.5 2.5-5 4-5z" fill="var(--white)"/>
      </svg>
      <span class="hotline-number">888 5550 1234</span>
    </div>
  </header>

  <nav class="main-nav">
    <a href="#" style="width:108px">Home</a>
    <a href="#" style="width:85px">Bios</a>
    <a href="#" style="width:183px">Product Review</a>
    <a href="#" style="width:134px">Activiities</a>
    <a href="#" style="width:151px">Case Studies</a>
    <a href="#" style="width:144px">Discussion</a>
    <a href="#" style="width:125px">Glossary</a>
    <a href="#" style="width:95px">FAQ</a>
    <a href="#" style="width:131px">Contact</a>
  </nav>

  <section class="hero">
    <h1 class="hero-title">How to<br>achieve your<br>target</h1>
    <div class="hero-art" role="img" aria-label="Illustration of darts hitting the centre of a target"></div>
  </section>
</body>
</html>
```